Stationery Design Project

We need a stationery design for our Norwegian trucking company. We have existed for about 15 years and our 12 drivers uses relatively new vehicles to transport goods around in northern Norway. Long distance routes with fresh fish og food transport is our main operations.

We have already made alogo that's printed on our trucks. The logo and a picture of our trucks is attached. I think the logo i crappy, but since its already in use, changing it is not an option in this round. Still using a better colour scheme in the overall stationery and more interesting fonts is possible (altso in the logo).

Company details:
Name: Kjelvraket AS
Organisation nr 873 615 309
Post adress: 8642 Raudvik

I like minimalism and simplicity. I am avalibly for questions in normal GMT working hours either here or on mail: ivar@fjordlast.no

Reason: Hi. Im extending the deadline because I needed some time to find a vector file of our logo. Sorry for the inconvenience

Hi, and thanks for all your interest in the project. Some updates:

-          I have decided to commit to using one of the designs. Some designer will get the payment.

-          I have extended the deadline with 24 hours since I needed some time to find our firms vector logo (a slow Swedish man was holding me up)

-          We will not choose a design before the deadline. No need to rush.

-          We have received a lot of great design and think there is a need to specified the product we want to make:

o   Business Card for all our employers. I just need the design and will duplicate with the correct numbers and name myself. The information on should be: Logo, employer’s name, Phone number, email, website, Postal number and address. Use this as a template: logo, Leif Brattvoll, 47382066, Leif@fjordlast.no,, fjordlast.no, 8642 Raudvik. The order and placement of the information is your creative decision.

o   Stickers to put on the goods we travel. On the sticker the should be the following information: Logo, phone number, Tekst and link: Fraktæ av Kjelvraket. Ke du syns? Fjordlast.no/tilbakemelding (this means: Handled by Kjelvraket. What do you think Fjordlast.no/feedback -à the link will be a feedback form). The placement the information and size is your creative decision with some stings: we have been thinking of using Drukko for printing and see that a size about 6x6 cm, 8x5 or something like that. (with 3000 copies our budget is 200 punds). Any suggestions of other suppliers are welcome. Drukko price calculator http://www.drukkolabelhouse.co.uk/digital-litho-printing/printing-labels-tags/stickers/

o   Letterhead with logo, address, phone number and organizational number.

o   Envelopes with logo,address, phone number and organizational number.

Have a nice day.

 

 

• Using the blue colour in the logo and using a similar graphic approch.

```html
<!DOCTYPE html>
<html lang="en">
<head>
<meta charset="utf-8">
<title>Kjelvraket AS – Stationery</title>
<link rel="stylesheet" href="https://fonts.googleapis.com/css2?family=Open+Sans:wght@400;600;700&display=swap">
<style>
  :root {
    --stage: #a6a6a6;
    --paper: #ffffff;
    --blue-deep: #21479a;
    --blue-mid: #1f7fb0;
    --blue-text: #1d74b8;
    --logo-blue: #1f3f98;
    --ink-grey: #6b6b6b;
    --line-dark: #222222;
  }
  html, body { margin: 0; padding: 0; overflow: hidden; }
  body {
    width: 1200px; height: 934px; position: relative;
    background: var(--paper);
    font-family: "Open Sans", Arial, sans-serif;
  }
  .stage { position: absolute; left: 0; top: 0; width: 1200px; height: 900px; background: var(--stage); }
  .sheet { position: absolute; background: var(--paper); overflow: hidden; }

  .brand {
    position: absolute; display: flex; align-items: center; gap: 8px;
    font-family: "Open Sans", Arial, sans-serif; font-weight: 700;
    color: var(--logo-blue); white-space: nowrap;
  }
  .brand .mark { border-radius: 50%; background: currentColor; flex: none; }
  .brand--light { color: #ffffff; }

  .contact { position: absolute; color: var(--ink-grey); font-size: 9px; line-height: 12px; }
  .contact .row { display: flex; align-items: center; gap: 4px; white-space: nowrap; }
  .contact svg { width: 7px; height: 7px; fill: var(--blue-text); flex: none; }
  .org { color: var(--blue-text); }

  /* Letterhead */
  .letterhead { left: 30px; top: 70px; width: 612px; height: 792px; }
  .letterhead .brand { left: 34px; top: 40px; font-size: 30px; }
  .letterhead .brand .mark { width: 24px; height: 24px; }
  .letterhead .contact { left: 496px; top: 49px; }
  .letterhead .wave { position: absolute; left: 0; bottom: 0; width: 612px; height: 180px; }
  .letterhead .footer-org { position: absolute; right: 10px; bottom: 6px; color: #e6eef8; font-size: 9px; }

  /* Business cards */
  .card-front {
    left: 735px; top: 50px; width: 252px; height: 144px; border-radius: 8px;
    background: radial-gradient(ellipse at 45% 80%, var(--blue-mid), var(--blue-deep) 75%);
  }
  .card-front .brand { left: 56px; top: 52px; font-size: 21px; }
  .card-front .brand .mark { width: 16px; height: 16px; }

  .card-back { left: 742px; top: 210px; width: 252px; height: 143px; border-radius: 8px; }
  .card-back .brand { left: 18px; top: 54px; font-size: 14px; gap: 5px; }
  .card-back .brand .mark { width: 11px; height: 11px; }
  .card-back .person { position: absolute; left: 150px; top: 34px; }
  .card-back .person-name { color: var(--blue-text); font-weight: 600; font-size: 9px; line-height: 11px; }
  .card-back .person-role { color: var(--ink-grey); font-size: 5.5px; line-height: 8px; }
  .card-back .contact { left: 150px; top: 70px; font-size: 5.5px; line-height: 9px; }
  .card-back .contact svg { width: 5px; height: 5px; }
  .card-back .wave { position: absolute; left: 0; bottom: 0; width: 252px; height: 143px; }

  /* Envelope */
  .envelope { position: absolute; left: 352px; top: 362px; width: 684px; height: 392px; }
  .envelope .flap { position: absolute; left: 0; top: 0; width: 684px; height: 96px; }
  .envelope .flap .brand { left: 294px; top: 38px; font-size: 14px; gap: 5px; transform: rotate(180deg); }
  .envelope .flap .brand .mark { width: 11px; height: 11px; }
  .envelope .body { left: 0; top: 94px; width: 684px; height: 298px; box-shadow: 0 0 2px rgba(0,0,0,.25); }
  .envelope .body .wave { position: absolute; left: 0; top: 0; width: 684px; height: 110px; }
  .envelope .body .brand { left: 16px; top: 100px; font-size: 22px; }
  .envelope .body .brand .mark { width: 18px; height: 18px; }
  .envelope .body .contact { left: 16px; top: 253px; }
</style>
</head>
<body>
<div class="stage">

  <section class="sheet letterhead">
    <div class="brand"><span class="mark"></span>Kjelvraket</div>
    <div class="contact">
      <div class="row"><svg viewBox="0 0 10 10"><path d="M5 0 L10 5 H8.5 V10 H6 V7 H4 V10 H1.5 V5 H0 Z"/></svg>8642 Raudvik</div>
      <div class="row"><svg viewBox="0 0 10 10"><path d="M1 3 Q5 0 9 3 L8 5 L6 4 V3 H4 V4 L2 5 Z M2 6 H8 V9 H2 Z"/></svg>47382066</div>
    </div>
    <svg class="wave" viewBox="0 0 612 180" preserveAspectRatio="none">
      <defs>
        <linearGradient id="lhBlue" x1="0" x2="1">
          <stop offset="0" stop-color="#21479a"/><stop offset=".5" stop-color="#1f7fb0"/><stop offset="1" stop-color="#21479a"/>
        </linearGradient>
        <linearGradient id="lhGrey" x1="0" x2="1">
          <stop offset=".35" stop-color="#ffffff"/><stop offset="1" stop-color="#555555"/>
        </linearGradient>
      </defs>
      <path d="M200,146 C300,156 420,158 500,140 C550,128 585,110 612,96" fill="none" stroke="url(#lhGrey)" stroke-width="6"/>
      <path d="M0,143 C150,122 300,152 410,150 C500,148 570,116 612,93" fill="none" stroke="#222" stroke-width="2.5"/>
      <path d="M0,150 C150,128 300,160 410,158 C500,156 570,130 612,108 L612,180 L0,180 Z" fill="url(#lhBlue)"/>
    </svg>
    <div class="footer-org">Organisation Number 873 615 309</div>
  </section>

  <section class="sheet card-front">
    <div class="brand brand--light"><span class="mark"></span>Kjelvraket</div>
  </section>

  <section class="sheet card-back">
    <div class="brand"><span class="mark"></span>Kjelvraket</div>
    <div class="person">
      <div class="person-name">Leif Brattvoll</div>
      <div class="person-role">Marketing Manager</div>
    </div>
    <div class="contact">
      <div class="row"><svg viewBox="0 0 10 10"><path d="M1 3 Q5 0 9 3 L8 5 L6 4 V3 H4 V4 L2 5 Z M2 6 H8 V9 H2 Z"/></svg>47382066</div>
      <div class="row"><svg viewBox="0 0 10 10"><path d="M0 2 H10 V8 H0 Z M1 3 L5 6 L9 3" fill="none" stroke="#1d74b8" stroke-width="1"/></svg>Leif@fjordlast.no</div>
      <div class="row"><svg viewBox="0 0 10 10"><circle cx="5" cy="5" r="5"/></svg>www.fjordlast.no</div>
      <div class="row"><svg viewBox="0 0 10 10"><path d="M5 0 L10 5 H8.5 V10 H6 V7 H4 V10 H1.5 V5 H0 Z"/></svg>8642 Raudvik</div>
    </div>
    <svg class="wave" viewBox="0 0 252 143" preserveAspectRatio="none">
      <defs>
        <linearGradient id="bcBlue" x1="0" x2="1">
          <stop offset="0" stop-color="#21479a"/><stop offset=".5" stop-color="#1f7fb0"/><stop offset="1" stop-color="#21479a"/>
        </linearGradient>
      </defs>
      <path d="M60,120 C120,126 180,124 215,112 C232,106 244,98 252,94" fill="none" stroke="#999" stroke-width="3"/>
      <path d="M0,115 C60,108 120,122 170,121 C210,120 240,104 252,96" fill="none" stroke="#222" stroke-width="1.5"/>
      <path d="M0,119 C60,112 120,126 170,125 C210,124 240,110 252,102 L252,143 L0,143 Z" fill="url(#bcBlue)"/>
    </svg>
  </section>

  <section class="envelope">
    <svg class="flap" viewBox="0 0 684 96" preserveAspectRatio="none">
      <defs>
        <radialGradient id="flapBlue" cx=".5" cy=".3" r=".6">
          <stop offset="0" stop-color="#1f7fb0"/><stop offset="1" stop-color="#21479a"/>
        </radialGradient>
      </defs>
      <path d="M0,96 L22,32 Q26,24 36,22 L341,0 L648,22 Q658,24 662,32 L684,96 Z" fill="url(#flapBlue)"/>
    </svg>
    <div class="flap">
      <div class="brand brand--light"><span class="mark"></span>Kjelvraket</div>
    </div>
    <div class="sheet body">
      <svg class="wave" viewBox="0 0 684 110" preserveAspectRatio="none">
        <defs>
          <linearGradient id="envBlue" x1="0" x2="1">
            <stop offset="0" stop-color="#21479a"/><stop offset=".5" stop-color="#1f7fb0"/><stop offset="1" stop-color="#21479a"/>
          </linearGradient>
          <linearGradient id="envGrey" x1="0" y1="0" x2="580" y2="0" gradientUnits="userSpaceOnUse">
            <stop offset="0" stop-color="#c8c8c8"/><stop offset=".45" stop-color="#8a8a8a"/><stop offset="1" stop-color="#ffffff"/>
          </linearGradient>
        </defs>
        <path d="M0,0 H684 V12 C670,20 650,30 620,30 C560,30 500,14 400,12 C250,10 120,32 0,70 Z" fill="url(#envBlue)"/>
        <path d="M0,78 C120,40 250,17 400,19 C470,20 520,26 580,32" fill="none" stroke="url(#envGrey)" stroke-width="6"/>
        <path d="M0,86 C120,48 250,24 400,26 C500,28 560,42 620,38 C650,36 670,28 684,20 L684,21.6 C670,29.6 650,38 620,40 C560,44.5 500,30.5 400,28.6 C250,28 120,53 0,91 Z" fill="#222"/>
      </svg>
      <div class="brand"><span class="mark"></span>Kjelvraket</div>
      <div class="contact">
        <div class="row"><svg viewBox="0 0 10 10"><path d="M5 0 L10 5 H8.5 V10 H6 V7 H4 V10 H1.5 V5 H0 Z"/></svg>8642 Raudvik</div>
        <div class="row"><svg viewBox="0 0 10 10"><path d="M1 3 Q5 0 9 3 L8 5 L6 4 V3 H4 V4 L2 5 Z M2 6 H8 V9 H2 Z"/></svg>47382066</div>
        <div class="row" style="margin-top:2px"><span class="org">Organisation Number</span>&nbsp;873 615 309</div>
      </div>
    </div>
  </section>

</div>
</body>
</html>
```